Landscape design build company door flyer

I would like this flyer to convey a high-level of professionalism for a company that is excellent with communication with their clients as well as a company that does incredible installations

Went on vacation/holiday

```html
<!DOCTYPE html>
<html lang="en">
<head>
<meta charset="utf-8">
<title>Cedar Ridge Builders – Door Flyer</title>
<link rel="stylesheet" href="https://fonts.googleapis.com/css2?family=Montserrat:wght@500;600;700;800&display=swap">
<style>
  :root {
    --navy: #15303f;
    --orange: #f26f13;
    --ink: #111417;
    --paper: #ffffff;
    --backdrop: #e9e9e9;
  }
  * { margin: 0; padding: 0; box-sizing: border-box; }
  html, body { width: 1200px; height: 933px; overflow: hidden; background: var(--backdrop); }
  body { font-family: "Montserrat", Arial, sans-serif; position: relative; }

  .flyer {
    position: absolute; left: 237px; top: 0;
    width: 1182px; height: 1520px;
    background: var(--paper);
    transform: scale(0.6138); transform-origin: 0 0;
    overflow: hidden;
  }
  .abs { position: absolute; }

  .hero-photo {
    left: 0; top: 371px; width: 1182px; height: 399px;
    background: linear-gradient(180deg, #3d4a3a 0%, #5a5f48 22%, #b1582c 38%, #a3512c 62%, #8b4a2c 74%, #7fae3f 86%, #6b9a36 100%);
  }
  .chevron, .banner-shape { left: 0; top: 0; }

  .brand { left: 27px; top: 175px; width: 360px; text-align: center; }
  .brand-dot { width: 48px; height: 48px; border-radius: 50%; background: var(--navy); margin: 0 auto 22px; }
  .brand-name { font-weight: 700; font-size: 25px; color: var(--navy); letter-spacing: 0.3px; line-height: 1; white-space: nowrap; }

  .headline { left: 499px; top: 78px; font-weight: 800; line-height: 1; }
  .headline-top { display: block; font-size: 84px; color: var(--navy); letter-spacing: 3px; }
  .headline-main { display: block; font-size: 146px; color: var(--orange); letter-spacing: 2px; margin-top: -6px; }

  .banner-text { left: 499px; top: 313px; font-weight: 700; font-size: 50px; line-height: 48px; color: var(--paper); letter-spacing: 0.5px; white-space: nowrap; }

  .gallery { left: 49px; top: 676px; width: 454px; height: 606px; background: var(--paper); }
  .gallery-photo { position: absolute; left: 8px; width: 438px; height: 178px; }
  .gallery-photo.paver { top: 7px; background: linear-gradient(160deg, #5b7a3c 0%, #7a6b57 35%, #9aa0a2 60%, #b3b7b8 100%); }
  .gallery-photo.stairs { top: 214px; background: linear-gradient(170deg, #6e8a5a 0%, #a87b55 30%, #8d8f88 60%, #6f9a48 100%); }
  .gallery-photo.deck { top: 421px; background: linear-gradient(180deg, #8a8f88 0%, #a98a6c 30%, #8e6d52 65%, #9c8a6d 100%); }

  .section-title { left: 541px; font-weight: 800; font-size: 31px; color: var(--navy); letter-spacing: 0.5px; }
  .rule { left: 541px; width: 571px; height: 3px; background: var(--ink); }
  .rule::before { content: ""; position: absolute; left: 0; top: 0; width: 142px; height: 5px; background: var(--orange); }

  .about-text { left: 545px; top: 854px; width: 568px; font-weight: 500; font-size: 20px; line-height: 24.8px; color: var(--ink); text-align: justify; hyphens: manual; }

  .services { left: 541px; top: 1173px; display: grid; grid-template-columns: 321px 300px; row-gap: 12px; list-style: none; }
  .services li { display: flex; align-items: center; gap: 18px; font-weight: 500; font-size: 21px; color: var(--navy); letter-spacing: 0.2px; height: 24.5px; white-space: nowrap; }
  .services svg { flex: none; }

  .cta-band { left: 0; top: 1324px; width: 1182px; height: 95px; background: var(--navy); display: flex; align-items: center; justify-content: center; }
  .cta-band span { font-weight: 800; font-size: 45px; color: var(--paper); letter-spacing: 1px; white-space: nowrap; }

  .contact { left: 0; top: 1436px; width: 1182px; display: flex; align-items: center; justify-content: center; gap: 16px; color: var(--navy); white-space: nowrap; }
  .contact-item { display: flex; align-items: center; gap: 10px; font-weight: 700; font-size: 19px; letter-spacing: 0.2px; flex: none; white-space: nowrap; }
  .contact-item.phone { font-size: 28px; }
  .contact-item svg { flex: none; }
  .divider { width: 3px; height: 34px; background: var(--ink); margin: 0 4px; flex: none; }
</style>
</head>
<body>
<div class="flyer">
  <div class="abs hero-photo" role="img" aria-label="Photo of a finished cedar wraparound porch with cross railings on a log home among tall trees"></div>

  <svg class="abs chevron" width="1182" height="440" viewBox="0 0 1182 440" aria-hidden="true">
    <polygon points="262,0 287,0 462,215 385,296 360,296 438,215" fill="var(--ink)"/>
  </svg>
  <svg class="abs banner-shape" width="1182" height="440" viewBox="0 0 1182 440" aria-hidden="true">
    <polygon points="372,296 1182,296 1182,427 259,427" fill="var(--navy)"/>
  </svg>

  <div class="abs brand">
    <div class="brand-dot"></div>
    <div class="brand-name">CEDAR RIDGE BUILDERS</div>
  </div>

  <h1 class="abs headline">
    <span class="headline-top">LOVE COMING</span>
    <span class="headline-main">HOME?</span>
  </h1>

  <p class="abs banner-text">LET US REIMAGINE YOUR<br>OUTDOOR LIVING AREA</p>

  <div class="abs gallery">
    <div class="gallery-photo paver" role="img" aria-label="Photo of a paver walkway with stone steps and a planted retaining wall"></div>
    <div class="gallery-photo stairs" role="img" aria-label="Photo of a two-level wooden deck with staircase and railings"></div>
    <div class="gallery-photo deck" role="img" aria-label="Photo of a low composite deck with wide wrap-around steps"></div>
  </div>

  <h2 class="abs section-title" style="top:800px;">ABOUT US</h2>
  <div class="abs rule" style="top:843px;"></div>
  <p class="abs about-text">Discover the endless possibilities for your outdoor space with The Cedar Ridge Builders Team. Our team of skilled artisans is dedicated to turning your outdoor space into a breathtaking oasis that you’ll love coming home to. Whether it’s a cozy patio for intimate gather­ings, a sprawling deck to host memorable parties, or a custom paver driveway that adds instant curb appeal, our high-quality craftsmanship ensures stunning results that exceed your expectations.</p>

  <h2 class="abs section-title" style="top:1104px;">OUR SERVICES</h2>
  <div class="abs rule" style="top:1147px;"></div>
  <ul class="abs services">
    <li><svg width="20" height="20" viewBox="0 0 20 20"><circle cx="10" cy="10" r="10" fill="var(--orange)"/><path d="M5.5 10.5l3 3 6-6.5" stroke="#fff" stroke-width="2.4" fill="none" stroke-linecap="round" stroke-linejoin="round"/></svg>PAVER PATIOS</li>
    <li><svg width="20" height="20" viewBox="0 0 20 20"><circle cx="10" cy="10" r="10" fill="var(--orange)"/><path d="M5.5 10.5l3 3 6-6.5" stroke="#fff" stroke-width="2.4" fill="none" stroke-linecap="round" stroke-linejoin="round"/></svg>POOLS</li>
    <li><svg width="20" height="20" viewBox="0 0 20 20"><circle cx="10" cy="10" r="10" fill="var(--orange)"/><path d="M5.5 10.5l3 3 6-6.5" stroke="#fff" stroke-width="2.4" fill="none" stroke-linecap="round" stroke-linejoin="round"/></svg>PAVER DRIVEWAYS</li>
    <li><svg width="20" height="20" viewBox="0 0 20 20"><circle cx="10" cy="10" r="10" fill="var(--orange)"/><path d="M5.5 10.5l3 3 6-6.5" stroke="#fff" stroke-width="2.4" fill="none" stroke-linecap="round" stroke-linejoin="round"/></svg>OUTDOOR LIGHTING</li>
    <li><svg width="20" height="20" viewBox="0 0 20 20"><circle cx="10" cy="10" r="10" fill="var(--orange)"/><path d="M5.5 10.5l3 3 6-6.5" stroke="#fff" stroke-width="2.4" fill="none" stroke-linecap="round" stroke-linejoin="round"/></svg>RETAINING WALLS</li>
    <li><svg width="20" height="20" viewBox="0 0 20 20"><circle cx="10" cy="10" r="10" fill="var(--orange)"/><path d="M5.5 10.5l3 3 6-6.5" stroke="#fff" stroke-width="2.4" fill="none" stroke-linecap="round" stroke-linejoin="round"/></svg>FIREPITS &amp; FIREPLACES</li>
    <li><svg width="20" height="20" viewBox="0 0 20 20"><circle cx="10" cy="10" r="10" fill="var(--orange)"/><path d="M5.5 10.5l3 3 6-6.5" stroke="#fff" stroke-width="2.4" fill="none" stroke-linecap="round" stroke-linejoin="round"/></svg>DECKS &amp; RAILINGS</li>
    <li><svg width="20" height="20" viewBox="0 0 20 20"><circle cx="10" cy="10" r="10" fill="var(--orange)"/><path d="M5.5 10.5l3 3 6-6.5" stroke="#fff" stroke-width="2.4" fill="none" stroke-linecap="round" stroke-linejoin="round"/></svg>AND MORE...</li>
  </ul>

  <div class="abs cta-band"><span>CONTACT US TODAY FOR A FREE ESTIMATE</span></div>

  <div class="abs contact">
    <div class="contact-item phone">
      <svg width="22" height="26" viewBox="0 0 24 24"><path d="M6.6 10.8a15.1 15.1 0 0 0 6.6 6.6l2.2-2.2c.3-.3.7-.4 1-.2 1.1.4 2.3.6 3.6.6.6 0 1 .4 1 1V20c0 .6-.4 1-1 1A17 17 0 0 1 3 4c0-.6.4-1 1-1h3.5c.6 0 1 .4 1 1 0 1.3.2 2.5.6 3.6.1.3 0 .7-.2 1z" fill="var(--orange)"/></svg>
      <span>206-555-0148</span>
    </div>
    <div class="divider"></div>
    <div class="contact-item">
      <svg width="28" height="20" viewBox="0 0 28 20"><rect x="0" y="0" width="28" height="20" rx="2" fill="var(--orange)"/><path d="M2 3l12 9 12-9" stroke="#fff" stroke-width="2.2" fill="none"/></svg>
      <span>INFO@CEDARRIDGEBUILDERS.COM</span>
    </div>
    <div class="divider"></div>
    <div class="contact-item">
      <svg width="26" height="26" viewBox="0 0 26 26" fill="none" stroke="var(--orange)" stroke-width="1.8"><circle cx="13" cy="13" r="11"/><ellipse cx="13" cy="13" rx="5" ry="11"/><path d="M2 13h22M4 7h18M4 19h18"/></svg>
      <span>WWW.CEDARRIDGEBUILDERS.COM</span>
    </div>
  </div>
</div>
</body>
</html>
```